HearthMile business card and stationary design

We are looking for a simple yet elegant design for our mortgage company business card and stationary.

The card should include:
Name (Marcus Pell)
Title (CEO)
Phone Number (732-555-0182)
Address (48 Birchwell Court, Suite 314, Fernwick, NJ 07000)
Email (email@hearthmile.example)
"NMLS" i.e. (NMLS 61947)
"Company NMLS" (Company NMLS 274615)

Contact Information for Business Card

See above

```html
<!DOCTYPE html>
<html lang="en">
<head>
<meta charset="utf-8">
<title>HearthMile Business Card</title>
<link href="https://fonts.googleapis.com/css2?family=Montserrat:wght@400;500;600;700&display=swap" rel="stylesheet">
<style>
  :root {
    --backdrop: #c9c9c9;
    --card: #29292a;
    --accent: #0aa7e8;
    --ink: #ffffff;
    --emboss: #3a3a3c;
  }
  * { box-sizing: border-box; margin: 0; padding: 0; }
  html, body {
    width: 1200px; height: 800px; overflow: hidden;
    background: var(--backdrop);
    font-family: "Montserrat", Arial, sans-serif;
  }
  .stage {
    width: 1200px; height: 800px;
    display: flex; align-items: center; justify-content: center; gap: 40px;
  }
  .card {
    position: relative;
    width: 540px; height: 309px;
    background: var(--card);
    border-radius: 22px;
    border-bottom: 2px solid var(--accent);
    box-shadow: 0 0 0 1px rgba(10,167,232,.35);
    color: var(--ink);
    overflow: hidden;
  }
  .brand-name {
    position: absolute; top: 62px; right: 38px;
    font-size: 56px; font-weight: 700; letter-spacing: .5px;
    line-height: 1; color: var(--ink);
  }
  .divider {
    position: absolute; top: 150px; left: 40px; right: 32px;
    height: 1px; background: var(--accent);
  }
  .person {
    position: absolute; top: 166px; left: 40px;
  }
  .person-name { font-size: 24px; font-weight: 700; color: var(--accent); line-height: 1.1; }
  .person-title { font-size: 15px; font-weight: 500; margin-bottom: 10px; }
  .contact-list { list-style: none; font-size: 12.5px; line-height: 1.55; }
  .contact-list li { display: flex; align-items: center; gap: 7px; }
  .contact-list svg { width: 13px; height: 13px; fill: var(--accent); flex: none; }
  .accent { color: var(--accent); }
  .licensing {
    position: absolute; top: 168px; right: 32px;
    text-align: right; font-size: 12.5px; line-height: 1.5;
  }
  .address { margin-top: 14px; }
  .card--back { display: flex; align-items: center; justify-content: center; }
  .back-name {
    font-size: 60px; font-weight: 700; letter-spacing: .5px;
    color: var(--emboss);
  }
</style>
</head>
<body>
<main class="stage">
  <section class="card card--front">
    <div class="brand-name">HearthMile</div>
    <div class="divider"></div>
    <div class="person">
      <p class="person-name">Marcus Pell</p>
      <p class="person-title">CEO</p>
      <ul class="contact-list">
        <li>
          <svg viewBox="0 0 24 24" aria-hidden="true"><path d="M6.6 10.8a15.1 15.1 0 0 0 6.6 6.6l2.2-2.2c.3-.3.7-.4 1-.2 1.1.4 2.3.6 3.6.6.6 0 1 .4 1 1V20c0 .6-.4 1-1 1A17 17 0 0 1 3 4c0-.6.4-1 1-1h3.5c.6 0 1 .4 1 1 0 1.3.2 2.5.6 3.6.1.3 0 .7-.2 1l-2.3 2.2z"/></svg>
          732-555-0182
        </li>
        <li>
          <svg viewBox="0 0 24 24" aria-hidden="true"><path d="M2 5h20v14H2zm2 2v.5l8 5 8-5V7l-8 5z"/></svg>
          email@hearthmile.example
        </li>
        <li>
          <svg viewBox="0 0 24 24" aria-hidden="true"><path d="M12 2a10 10 0 1 0 0 20 10 10 0 0 0 0-20zm6.9 9h-3a15 15 0 0 0-1.2-5.5A8 8 0 0 1 18.9 11zM12 4c.9 1.2 1.8 3.6 1.9 7h-3.8C10.2 7.6 11.1 5.2 12 4zM9.3 5.5A15 15 0 0 0 8.1 11h-3a8 8 0 0 1 4.2-5.5zM5.1 13h3a15 15 0 0 0 1.2 5.5A8 8 0 0 1 5.1 13zM12 20c-.9-1.2-1.8-3.6-1.9-7h3.8c-.1 3.4-1 5.8-1.9 7zm2.7-1.5a15 15 0 0 0 1.2-5.5h3a8 8 0 0 1-4.2 5.5z"/></svg>
          <span>www.<span class="accent">hearthmile</span>.example</span>
        </li>
      </ul>
    </div>
    <div class="licensing">
      <p><span class="accent">NMLS</span> 61947</p>
      <p><span class="accent">Company NMLS</span> 274615</p>
      <p class="address">48 Birchwell Court, Suite 314,<br>Fernwick, NJ 07000</p>
    </div>
  </section>

  <section class="card card--back">
    <div class="back-name">HearthMile</div>
  </section>
</main>
</body>
</html>
```